New Business Card for Web Design/Internet Marketing Company

Looking for a great looking new business card. We are a 10 year old web design, internet marketing and website management company that works mostly with small businesses.

Our new card needs to better match the colors and style of our website, be bold, extremely usable and slightly edgy.

Target Market(s)

Small/Medium businesses that have websites

Industry/Entity Type

Internet

Requirements
Must have
• Front and back design, full color, rounded corners please

Must use the colors/style of our website (JPG provided)

INFO FOR CARDS (as readable as possible please)
Mark Lenner
President/CEO
mark@trelvanmedia.example
Phone: 520-381-7459
Toll Free: 866-381-7459
Address: 4315 W. Calloway Ave. Ste. 140, Tucson, AZ 85792

THINGS I WANT TO PROMOTE (if there is room):
1. Our Website - www.trelvanmedia.example

2. Social Media
Twitter: @trelvanmedia
Facebook: www.facebook.com/trelvanmedia

3. Our Services
Web Design
Internet Marketing
Website Management

```html
<!DOCTYPE html>
<html lang="en">
<head>
<meta charset="utf-8">
<title>Trelvan Media – Business Card</title>
<link rel="stylesheet" href="https://fonts.googleapis.com/css2?family=Open+Sans:wght@400;600;700&display=swap">
<style>
  :root {
    --brand-blue: #1d8fcb;
    --brand-orange: #f27f24;
    --ink: #4a4a4a;
    --paper: #ffffff;
    --backdrop: #e9e6e2;
  }
  * { margin: 0; padding: 0; box-sizing: border-box; }
  html, body { width: 1200px; height: 402px; overflow: hidden; }
  body {
    background: var(--backdrop);
    font-family: "Open Sans", Arial, sans-serif;
    position: relative;
  }
  .card {
    position: absolute;
    top: 58px;
    width: 512px;
    height: 292px;
    border-radius: 6px;
    overflow: hidden;
    box-shadow: 0 2px 6px rgba(0,0,0,.18);
  }
  .card--front { left: 62px; background: var(--paper); }
  .card--back { left: 627px; background: var(--brand-blue); color: #fff; }

  .swoosh { position: absolute; inset: 0; width: 100%; height: 100%; }

  /* Front */
  .brand {
    position: absolute; left: 34px; top: 130px;
    display: flex; align-items: center; gap: 8px;
  }
  .brand__dot {
    width: 18px; height: 18px; border-radius: 50%;
    background: var(--brand-blue);
  }
  .brand__name {
    font-weight: 700; font-size: 30px; line-height: 1;
    color: var(--brand-orange); letter-spacing: -0.3px;
  }
  .tagline {
    position: absolute; left: 60px; width: 212px; top: 168px;
    text-align: right; font-size: 13px; color: var(--ink);
  }
  .address {
    position: absolute; left: 20px; width: 260px; top: 208px;
    text-align: right; font-size: 12.5px; line-height: 19px; color: var(--ink);
  }
  .person { position: absolute; left: 306px; top: 152px; }
  .person__name { font-size: 17px; font-weight: 600; color: var(--brand-blue); line-height: 20px; }
  .person__title { font-size: 11.5px; color: var(--brand-blue); line-height: 15px; }
  .person__rule { width: 98px; height: 2px; background: var(--brand-blue); margin-top: 5px; }
  .contacts {
    position: absolute; left: 306px; top: 210px; list-style: none;
    font-size: 12.5px; line-height: 18.5px; color: var(--ink);
  }
  .contacts li { display: flex; align-items: center; gap: 5px; white-space: nowrap; }
  .contacts svg { width: 10px; height: 10px; flex: none; }

  /* Back */
  .back__brand {
    position: absolute; left: 0; right: 0; top: 70px;
    display: flex; justify-content: center; align-items: center; gap: 10px;
  }
  .back__brand .brand__dot { background: #fff; width: 20px; height: 20px; }
  .back__brand .brand__name { color: #fff; font-size: 40px; }
  .services { position: absolute; left: 0; right: 0; top: 156px; text-align: center; }
  .services__title {
    display: inline-block; font-size: 21px; font-weight: 600;
    padding: 0 14px 2px; border-bottom: 2px solid #fff;
  }
  .services__list { margin-top: 12px; font-size: 17.5px; line-height: 26px; }
  .social {
    position: absolute; left: 0; right: 0; top: 266px;
    display: flex; justify-content: center; gap: 36px; font-size: 12px;
  }
  .social span { display: flex; align-items: center; gap: 5px; }
  .social i { width: 11px; height: 11px; background: rgba(255,255,255,.85); display: inline-block; border-radius: 2px; }
</style>
</head>
<body>

<section class="card card--front" aria-label="Card front">
  <svg class="swoosh" viewBox="0 0 512 292" preserveAspectRatio="none" aria-hidden="true">
    <path d="M380 0 H512 V72 C480 40 440 16 380 0 Z" fill="var(--brand-blue)"/>
    <path d="M360 0 C430 14 484 40 512 76" fill="none" stroke="var(--brand-orange)" stroke-width="3"/>
    <path d="M0 226 C60 262 160 284 330 292 H0 Z" fill="var(--brand-blue)"/>
    <path d="M0 214 C70 256 180 280 350 292" fill="none" stroke="var(--brand-orange)" stroke-width="3"/>
  </svg>

  <div class="brand">
    <span class="brand__dot"></span>
    <span class="brand__name">Trelvan Media</span>
  </div>
  <p class="tagline">Build your Presence</p>

  <p class="address">4315 W. Calloway Ave. Ste. 140<br>Tucson, AZ 85792</p>

  <div class="person">
    <p class="person__name">Mark Lenner</p>
    <p class="person__title">President/CEO</p>
    <div class="person__rule"></div>
  </div>

  <ul class="contacts">
    <li><svg viewBox="0 0 10 10"><circle cx="5" cy="5" r="5" fill="var(--brand-blue)"/><path d="M3 2.5 L4.3 3.8 L3.8 4.6 Q4.6 6 5.6 6.3 L6.3 5.8 L7.6 7 L6.8 7.8 Q4 7.6 2.3 3.3 Z" fill="#fff"/></svg>520-381-7459</li>
    <li><svg viewBox="0 0 10 10"><circle cx="5" cy="5" r="5" fill="var(--brand-blue)"/><path d="M3 2.5 L4.3 3.8 L3.8 4.6 Q4.6 6 5.6 6.3 L6.3 5.8 L7.6 7 L6.8 7.8 Q4 7.6 2.3 3.3 Z" fill="#fff"/></svg>866-381-7459</li>
    <li><svg viewBox="0 0 10 10"><rect x="0" y="2" width="10" height="7" fill="var(--brand-blue)"/><path d="M0 2 L5 6 L10 2" fill="none" stroke="#fff" stroke-width="1"/></svg>mark@trelvanmedia.example</li>
    <li><svg viewBox="0 0 10 10"><circle cx="5" cy="5" r="4.4" fill="none" stroke="var(--brand-blue)" stroke-width="1.2"/><ellipse cx="5" cy="5" rx="1.8" ry="4.4" fill="none" stroke="var(--brand-blue)" stroke-width="1"/><path d="M0.6 5 H9.4" stroke="var(--brand-blue)" stroke-width="1"/></svg>www.trelvanmedia.example</li>
  </ul>
</section>

<section class="card card--back" aria-label="Card back">
  <div class="back__brand">
    <span class="brand__dot"></span>
    <span class="brand__name">Trelvan Media</span>
  </div>
  <div class="services">
    <h2 class="services__title">Our Services</h2>
    <p class="services__list">Web Design &nbsp;•&nbsp; Internet Marketing<br>Website Management</p>
  </div>
  <div class="social">
    <span><i></i>@trelvanmedia</span>
    <span><i></i>trelvanmedia</span>
  </div>
</section>

</body>
</html>
```